New Business Card for Web Design/Internet Marketing Company

Looking for a great looking new business card. We are a 10 year old web design, internet marketing and website management company that works mostly with small businesses.

Our new card needs to better match the colors and style of our website, be bold, extremely usable and slightly edgy.

Target Market(s)

Small/Medium businesses that have websites

Industry/Entity Type

Internet

Requirements
Must have
• Front and back design, full color, rounded corners please

Must use the colors/style of our website (JPG provided)

INFO FOR CARDS (as readable as possible please)
Mark Lenner
President/CEO
mark@trelvanmedia.example
Phone: 520-381-7459
Toll Free: 866-381-7459
Address: 4315 W. Calloway Ave. Ste. 140, Tucson, AZ 85792

THINGS I WANT TO PROMOTE (if there is room):
1. Our Website - www.trelvanmedia.example

2. Social Media
Twitter: @trelvanmedia
Facebook: www.facebook.com/trelvanmedia

3. Our Services
Web Design
Internet Marketing
Website Management

```html
<!DOCTYPE html>
<html lang="en">
<head>
<meta charset="utf-8">
<title>Trelvan Media – Business Card</title>
<link href="https://fonts.googleapis.com/css2?family=Ubuntu:wght@400;500;700&display=swap" rel="stylesheet">
<style>
  :root {
    --brand-blue: #1b95cf;
    --brand-blue-deep: #1583b8;
    --brand-blue-soft: #4fb0de;
    --brand-orange: #f0882e;
    --ink: #4a4a4a;
    --paper: #ffffff;
    --stage: #ececec;
  }
  * { box-sizing: border-box; margin: 0; padding: 0; }
  html, body { width: 1200px; height: 402px; overflow: hidden; }
  body {
    background: var(--stage);
    font-family: "Ubuntu", sans-serif;
    position: relative;
  }
  .card {
    position: absolute;
    top: 56px;
    height: 290px;
    border-radius: 12px;
    overflow: hidden;
  }
  /* Front */
  .card-front {
    left: 60px;
    width: 538px;
    background: var(--paper);
  }
  .front-band {
    position: absolute; left: 0; top: 0; bottom: 0;
    width: 87px;
    background: var(--brand-blue);
    border-right: 3px solid var(--brand-orange);
  }
  .front-logo {
    position: absolute; left: 40px; top: 58px;
    display: flex; align-items: center; gap: 14px;
  }
  .logo-dot {
    width: 40px; height: 40px; border-radius: 50%;
    background: var(--brand-orange);
    flex: none;
  }
  .front-logo .logo-name {
    font-size: 40px; font-weight: 700; color: var(--brand-blue);
    letter-spacing: -0.5px;
    white-space: nowrap;
  }
  .contact {
    position: absolute; left: 138px; top: 148px;
    color: var(--ink);
  }
  .contact-name {
    font-size: 16px; font-weight: 500; color: var(--brand-blue);
    margin-bottom: 18px;
  }
  .contact-title { font-size: 12px; font-weight: 400; }
  .contact-list { list-style: none; font-size: 12.5px; line-height: 18.5px; }
  .contact-list li { display: flex; align-items: center; gap: 5px; }
  .contact-list svg { width: 9px; height: 9px; fill: var(--brand-blue); flex: none; }
  .contact-address { font-size: 12.5px; margin-top: 10px; }
  /* Back */
  .card-back {
    left: 626px;
    width: 512px;
    background: var(--brand-blue);
    color: var(--paper);
  }
  .back-mark {
    position: absolute; left: 22px; top: 0; bottom: 0;
    width: 220px;
    display: flex; align-items: center; gap: 10px;
  }
  .back-mark .logo-dot { width: 26px; height: 26px; background: var(--paper); }
  .back-mark .logo-name {
    font-size: 26px; font-weight: 700; color: var(--paper);
    white-space: nowrap;
  }
  .social {
    position: absolute; left: 272px; top: 42px;
    list-style: none; font-size: 15px; line-height: 22px;
  }
  .social li { display: flex; align-items: center; gap: 10px; }
  .social-chip {
    width: 15px; height: 15px; border-radius: 2px;
    background: var(--brand-blue-soft); flex: none;
  }
  .services { position: absolute; left: 272px; top: 117px; }
  .services h2 { font-size: 25px; font-weight: 500; margin-bottom: 14px; }
  .services ul { list-style: none; font-size: 21px; line-height: 31px; }
</style>
</head>
<body>
  <section class="card card-front" aria-label="Card front">
    <div class="front-band"></div>
    <div class="front-logo">
      <span class="logo-dot"></span>
      <span class="logo-name">Trelvan Media</span>
    </div>
    <div class="contact">
      <p class="contact-name">Mark Lenner, <span class="contact-title">President/CEO</span></p>
      <ul class="contact-list">
        <li><svg viewBox="0 0 10 10"><circle cx="5" cy="5" r="5"/></svg>520-381-7459</li>
        <li><svg viewBox="0 0 10 10"><circle cx="5" cy="5" r="5"/></svg>866-381-7459</li>
        <li><svg viewBox="0 0 10 10"><rect x="0" y="2" width="10" height="7"/></svg>mark@trelvanmedia.example</li>
        <li><svg viewBox="0 0 10 10"><circle cx="5" cy="5" r="5"/></svg>www.trelvanmedia.example</li>
      </ul>
      <p class="contact-address">4315 W. Calloway Ave. Ste. 140, Tucson, AZ 85792</p>
    </div>
  </section>

  <section class="card card-back" aria-label="Card back">
    <div class="back-mark">
      <span class="logo-dot"></span>
      <span class="logo-name">Trelvan Media</span>
    </div>
    <ul class="social">
      <li><span class="social-chip"></span>@trelvanmedia</li>
      <li><span class="social-chip"></span>trelvanmedia</li>
    </ul>
    <div class="services">
      <h2>Our Services</h2>
      <ul>
        <li>Web Design</li>
        <li>Internet Marketing</li>
        <li>Website Management</li>
      </ul>
    </div>
  </section>
</body>
</html>
```